Brightfen Business Card Redesign & Logo Update

We need to update our business cards to something more modern and fresh. Brightfen can provide the current color schemes and old design examples, but welcome creativity in helping us with this redesign. PLEASE NOTE that we no longer utilize the "tree" and/or "leaf" imagery in our branding. If able would apprecaite an update on the quality of our "words only" logo in Ai. / PNG formats too.

Target Market(s)

Investors, landowners, corporate partners, contractors

Industry/Entity Type

Environmental Restoration & Conservation

Contact Information for Business Card

Logo, persons name, title, mailing address, phone and email, website url

Font styles to use
Other font styles liked:
• Merriweather

Requirements
Nice to have
• Logo, persons name, title, mailing address, phone and email, website url, but open to ideams
Should not have
• No all back backgrounds

```html
<!DOCTYPE html>
<html lang="en">
<head>
<meta charset="utf-8">
<title>Brightfen Business Card</title>
<link rel="stylesheet" href="https://fonts.googleapis.com/css2?family=Oswald:wght@400;500;600&display=swap">
<style>
  :root {
    --backdrop: #5b5b5b;
    --card-front: #ffffff;
    --card-back: #0f5a2c;
    --orange: #ee7a08;
    --green: #107c38;
    --ink: #111111;
    --back-mark: #f2f5f0;
    --back-tagline: #a9d3b3;
  }
  * { margin: 0; padding: 0; box-sizing: border-box; }
  html, body {
    width: 1093px;
    height: 1200px;
    overflow: hidden;
    background: var(--backdrop);
    font-family: "Oswald", "Arial Narrow", sans-serif;
  }
  .canvas { position: relative; width: 1093px; height: 1200px; }

  .card {
    position: absolute;
    left: 264px;
    width: 580px;
    height: 356px;
    border-radius: 30px;
    overflow: hidden;
  }
  .card--front { top: 226px; background: var(--card-front); color: var(--ink); }
  .card--back { top: 621px; background: var(--card-back); }

  .holder { position: absolute; left: 34px; top: 68px; line-height: 1; }
  .holder__name {
    font-weight: 500;
    font-size: 32px;
    letter-spacing: -0.3px;
    color: var(--green);
  }
  .holder__name .first { color: var(--orange); }
  .holder__title { font-weight: 400; font-size: 19px; letter-spacing: -0.3px; margin-top: 1px; }

  .wordmark { position: absolute; text-align: center; line-height: 1; }
  .card--front .wordmark { left: 272px; top: 54px; width: 266px; }
  .wordmark__name {
    display: block;
    font-weight: 600;
    font-size: 56px;
    letter-spacing: 0.5px;
    color: var(--green);
  }
  .wordmark__tagline {
    display: block;
    font-weight: 500;
    font-size: 18px;
    letter-spacing: -0.2px;
    margin-top: 3px;
  }

  .contacts { position: absolute; left: 34px; top: 256px; list-style: none; }
  .contacts li {
    display: flex;
    align-items: center;
    gap: 8px;
    font-size: 18px;
    line-height: 21.5px;
    letter-spacing: -0.3px;
  }
  .contacts svg { width: 15px; height: 15px; flex: none; }

  .address {
    position: absolute;
    right: 36px;
    top: 278px;
    text-align: right;
    font-style: normal;
    font-size: 18px;
    line-height: 21.5px;
    letter-spacing: -0.3px;
  }

  .card--back .wordmark { left: 0; right: 0; top: 128px; }
  .card--back .wordmark__name { font-size: 68px; color: var(--back-mark); letter-spacing: 1.5px; }
  .card--back .wordmark__tagline { font-size: 22px; color: var(--back-tagline); margin-top: 0; }
</style>
</head>
<body>
<main class="canvas">
  <section class="card card--front" aria-label="Business card front">
    <div class="holder">
      <p class="holder__name"><span class="first">MARCUS</span> HALE</p>
      <p class="holder__title">Managing Director</p>
    </div>

    <div class="wordmark">
      <span class="wordmark__name">BRIGHTFEN</span>
      <span class="wordmark__tagline">ENVIRONMENTAL CREDIT COMPANY</span>
    </div>

    <ul class="contacts">
      <li>
        <svg viewBox="0 0 16 16" aria-hidden="true"><path fill="none" stroke="var(--orange)" stroke-width="1.8" stroke-linecap="round" d="M3.5 2 L6 4.5 L4.8 6.5 Q6.5 9.8 9.5 11.2 L11.5 10 L14 12.5 L12.3 14.2 Q6 13.5 1.8 3.7 Z M9 2.2 Q13.5 2.7 13.8 7 M9 4.8 Q11 5 11.2 7"/></svg>
        <span>044-987 654 321</span>
      </li>
      <li>
        <svg viewBox="0 0 16 16" aria-hidden="true"><rect x="0.5" y="3" width="15" height="10" fill="var(--orange)"/><path d="M0.5 3 L8 9 L15.5 3 M0.5 13 L6 8 M15.5 13 L10 8" fill="none" stroke="#fff" stroke-width="1.1"/></svg>
        <span>hello@brightfen.com</span>
      </li>
      <li>
        <svg viewBox="0 0 16 16" aria-hidden="true"><g fill="none" stroke="var(--orange)" stroke-width="1.3"><circle cx="8" cy="8" r="6.8"/><ellipse cx="8" cy="8" rx="3" ry="6.8"/><path d="M1.2 8 H14.8 M2.2 4.6 H13.8 M2.2 11.4 H13.8 M8 1.2 V14.8"/></g></svg>
        <span>www.brightfen.com</span>
      </li>
    </ul>

    <address class="address">
      88, Fenmoor Road, Suite 4<br>
      45210, Northvale
    </address>
  </section>

  <section class="card card--back" aria-label="Business card back">
    <div class="wordmark">
      <span class="wordmark__name">BRIGHTFEN</span>
      <span class="wordmark__tagline">ENVIRONMENTAL CREDIT COMPANY</span>
    </div>
  </section>
</main>
</body>
</html>
```